Looking for a modern, Professional business card design

We have a simple business card, but are looking for a more modern, professional look. A sample of the basic card is attached as well as the logo. We would also like to add that we offer:
Struggling with your finances?
- Learn to become debt free
- Discover the power of cash
- Control your money instead of it controlling you
Let us help you achieve a new level of financial freedom!
Also, we would like to have a "SPECIAL OFFER!: FREE 30 minute consultation"
Financial Planning

```html
<!DOCTYPE html>
<html lang="en">
<head>
<meta charset="utf-8">
<title>Liberty Money Coaching – Business Card</title>
<link rel="stylesheet" href="https://fonts.googleapis.com/css2?family=Roboto:wght@400;500;700;900&display=swap">
<style>
  :root {
    --stage: #3a3b3d;
    --green-dark: #2f7d12;
    --green: #4a9e1c;
    --green-light: #8ccc3c;
    --card-white: #ffffff;
    --panel-dark: #2b2c2e;
    --panel-mid: #45474a;
    --ink: #1c1c1c;
    --text-light: #f2f2f2;
    --text-soft: #d7d9db;
  }
  * { box-sizing: border-box; margin: 0; padding: 0; }
  html, body { width: 1200px; height: 950px; overflow: hidden; }
  body {
    background: var(--stage);
    font-family: "Roboto", Arial, sans-serif;
    position: relative;
  }
  .card {
    position: absolute;
    left: 250px;
    width: 700px;
    height: 400px;
    overflow: hidden;
    border-radius: 4px;
    box-shadow: 0 12px 30px rgba(0,0,0,.35);
  }

  /* Back side */
  .card-back {
    top: 50px;
    background: radial-gradient(ellipse at 55% 35%, var(--green-light) 0%, var(--green) 45%, var(--green-dark) 100%);
    color: var(--text-light);
    text-align: center;
    padding-top: 58px;
  }
  .brand {
    display: inline-flex;
    align-items: center;
    gap: 14px;
  }
  .brand-dot {
    width: 34px; height: 34px; border-radius: 50%;
  }
  .brand-name {
    font-weight: 900;
    font-size: 40px;
    letter-spacing: 1px;
    text-transform: uppercase;
  }
  .card-back .brand-dot { background: var(--text-light); }
  .card-back .brand-name { color: var(--text-light); }
  .pitch-heading {
    margin-top: 48px;
    font-weight: 700;
    font-size: 24px;
    letter-spacing: .5px;
  }
  .pitch-list {
    margin-top: 12px;
    font-size: 19px;
    line-height: 1.5;
    list-style: none;
  }
  .pitch-close { font-size: 19px; margin-top: 4px; }
  .offer {
    margin-top: 22px;
    font-weight: 700;
    font-size: 22px;
  }

  /* Front side */
  .card-front {
    top: 500px;
    background: var(--card-white);
  }
  .front-panel {
    position: absolute; inset: 0;
  }
  .card-front .brand {
    position: absolute;
    left: 40px; top: 150px;
  }
  .card-front .brand-dot { background: var(--green); }
  .card-front .brand-name { color: var(--ink); font-size: 30px; }
  .contact {
    position: absolute;
    right: 46px; top: 80px;
    text-align: right;
    color: var(--text-light);
  }
  .contact-name { font-size: 30px; font-weight: 500; }
  .contact-role { font-size: 19px; color: var(--text-soft); margin-top: 4px; }
  .contact-phone { font-size: 19px; margin-top: 36px; }
  .contact-phone b { font-weight: 700; }
  .contact-lines { margin-top: 36px; font-size: 18px; line-height: 1.6; color: var(--text-soft); }
</style>
</head>
<body>

<section class="card card-back">
  <div class="brand">
    <span class="brand-dot"></span>
    <span class="brand-name">Liberty Money Coaching</span>
  </div>
  <h2 class="pitch-heading">STRUGGLING WITH YOUR FINANCES?</h2>
  <ul class="pitch-list">
    <li>Learn to become debt free • Discover the power of cash</li>
    <li>Control your money instead of it controlling you</li>
  </ul>
  <p class="pitch-close">Achieve a new level of financial freedom!</p>
  <p class="offer">SPECIAL OFFER! FREE 30 minute consultation</p>
</section>

<section class="card card-front">
  <svg class="front-panel" viewBox="0 0 700 400" width="700" height="400">
    <defs>
      <linearGradient id="panelShade" x1="0" y1="0" x2="1" y2="1">
        <stop offset="0" stop-color="var(--panel-mid)"/>
        <stop offset="1" stop-color="var(--panel-dark)"/>
      </linearGradient>
    </defs>
    <path d="M360 0 L700 0 L700 400 L300 400 C 370 300, 330 120, 360 0 Z" fill="url(#panelShade)"/>
    <path d="M360 0 C 330 120, 370 300, 300 400" fill="none" stroke="var(--green)" stroke-width="6"/>
  </svg>
  <div class="brand">
    <span class="brand-dot"></span>
    <span class="brand-name">Liberty Money<br>Coaching</span>
  </div>
  <div class="contact">
    <p class="contact-name">Daniel R. Hayes</p>
    <p class="contact-role">Personal Financial Coach</p>
    <p class="contact-phone"><b>Mob:</b> (205) 555-0187</p>
    <p class="contact-lines">daniel@steadyledgercoaching.com<br>www.steadyledgercoaching.com</p>
  </div>
</section>

</body>
</html>
```